Building company buisness cards

We are looking for a sharp modern new look for our business cards.
We are a New Zealand based company that specialises in house and land packages.
We have attached a photo of the current logo and would like to see if it can be improved somehow if needed.
We are open to any colours but we have chosen green at this stage.
Feel free to change the font and make the logo smarter looking.
Play with the colours and see what looks best.

We want a card that looks so good know one will want to throw it away!

Target Market(s)

Home buyers

Industry/Entity Type

Building

Contact Information for Business Card

Derek Tolvane
0217394062
dtolvane@quillmarkhomesteads.co.nz
quillmarkhomesteads.co.nz

Font styles to use
Serif
Sans Serif

Colors

Designer to choose colors to be used in the design.

Requirements
Must have
• Logo and company name on one side, details on the other side
Nice to have
• Color codes for the original green are HEX #4a8028, RGB(74,128,40), CMYK(42,0,69,50)
• Round corners, Raised and/or spot UV

```html
<!DOCTYPE html>
<html lang="en">
<head>
<meta charset="utf-8">
<title>Quillmark Homesteads – Business Card</title>
<link rel="stylesheet" href="https://fonts.googleapis.com/css2?family=Roboto:wght@400;500&family=Roboto+Condensed:wght@400&family=Open+Sans:wght@600&family=Hind:wght@700&display=swap">
<style>
  :root {
    --backdrop: #2b2b2b;
    --card-white: #ffffff;
    --brand-green: #4a8028;
    --band-grey: #8c8b8c;
    --back-grey: #565656;
    --text-white: #ffffff;
    --rule-grey: #8a8a8a;
  }
  * { margin: 0; padding: 0; box-sizing: border-box; }
  html, body {
    width: 1125px;
    height: 1200px;
    overflow: hidden;
    background: var(--backdrop);
  }
  .card {
    position: absolute;
    left: 162px;
    width: 800px;
    height: 456px;
    overflow: hidden;
  }
  .card-front { top: 110px; background: var(--card-white); }
  .card-back { top: 632px; background: var(--back-grey); }

  .front-shapes { position: absolute; inset: 0; }

  .brand-name {
    position: absolute;
    right: 50px;
    top: 150px;
    text-align: center;
    font-family: "Open Sans", sans-serif;
    font-weight: 600;
    color: var(--brand-green);
    font-size: 44px;
    line-height: 1.05;
    letter-spacing: -0.5px;
  }

  .contact-block {
    position: absolute;
    left: 39px;
    top: 302px;
    color: var(--text-white);
  }
  .person-name {
    font-family: "Roboto", sans-serif;
    font-weight: 500;
    font-size: 29px;
    letter-spacing: 0.3px;
    margin-bottom: 14px;
  }
  .contact-list { list-style: none; }
  .contact-item {
    display: flex;
    align-items: center;
    gap: 11px;
    font-family: "Roboto Condensed", sans-serif;
    font-size: 19.5px;
    height: 26px;
  }
  .contact-icon { width: 18px; height: 18px; flex: none; fill: var(--text-white); }

  .back-lockup {
    position: absolute;
    left: 0; right: 0;
    top: 184px;
    text-align: center;
    color: var(--text-white);
  }
  .back-name {
    font-family: "Hind", sans-serif;
    font-weight: 700;
    line-height: 0.95;
  }
  .back-name .line-small { display: block; font-size: 38px; }
  .back-name .line-large { display: block; font-size: 46px; }
  .back-rule {
    width: 84px;
    height: 1px;
    background: var(--rule-grey);
    margin: 12px auto 8px;
  }
  .back-url {
    font-family: "Roboto", sans-serif;
    font-weight: 400;
    font-size: 18px;
    letter-spacing: 2px;
  }
</style>
</head>
<body>
  <section class="card card-front">
    <svg class="front-shapes" width="800" height="456" viewBox="0 0 800 456" aria-hidden="true">
      <path d="M0 277 H335 Q345 277 351 286 L460 456 H0 Z" fill="var(--brand-green)"/>
      <path d="M447 431 H800 V456 H463 Z" fill="var(--band-grey)"/>
    </svg>

    <div class="brand-name">Quillmark<br>Homesteads</div>

    <div class="contact-block">
      <div class="person-name">DEREK TOLVANE</div>
      <ul class="contact-list">
        <li class="contact-item">
          <svg class="contact-icon" viewBox="0 0 24 24"><path d="M6.6 10.8c1.4 2.8 3.8 5.1 6.6 6.6l2.2-2.2c.3-.3.7-.4 1-.2 1.1.4 2.3.6 3.6.6.6 0 1 .4 1 1V20c0 .6-.4 1-1 1C10.6 21 3 13.4 3 4c0-.6.4-1 1-1h3.5c.6 0 1 .4 1 1 0 1.3.2 2.5.6 3.6.1.3 0 .7-.2 1z"/></svg>
          <span>0217394062</span>
        </li>
        <li class="contact-item">
          <svg class="contact-icon" viewBox="0 0 24 24"><path d="M3 6h18v1.2l-9 5.6-9-5.6z M3 9.4l9 5.6 9-5.6V18H3z"/></svg>
          <span>dtolvane@quillmarkhomesteads.co.nz</span>
        </li>
        <li class="contact-item">
          <svg class="contact-icon" viewBox="0 0 24 24"><circle cx="12" cy="12" r="9.5"/><path d="M7 7.5l3 1.2 1 3-2 1.5.5 3.5L7 15l-1.5-4z M14 5l3 2-1 3 2 2 1.5-1M13.5 14l2.5 1-1 4-2-1z" fill="var(--brand-green)"/></svg>
          <span>quillmarkhomesteads.co.nz</span>
        </li>
      </ul>
    </div>
  </section>

  <section class="card card-back">
    <div class="back-lockup">
      <div class="back-name">
        <span class="line-small">quillmark</span>
        <span class="line-large">homesteads.</span>
      </div>
      <div class="back-rule"></div>
      <div class="back-url">www.quillmarkhomesteads.co.nz</div>
    </div>
  </section>
</body>
</html>
```